Business cards for KORU Real Estate Holdings LLC

We need a cool, original business card design for a company based in the Washington DC metropolitan area. We are a new energetic and passionate Real Estate Investing Company that invests in all types of real estate; commercial, residential, industrial etc.

Our company color is Red since it reflects action, energy and speed; it is assertive confident, energizing, exciting, powerful, passionate and determined. So we would like business card communicate those qualities to the audience.

Our audiences are investors that want to invest with us, real estate sellers, buyers, and tenants who lease from us.

Our logo is attached

```html
<!DOCTYPE html>
<html lang="en">
<head>
<meta charset="utf-8">
<title>KORU Real Estate Holdings LLC — Business Card</title>
<link href="https://fonts.googleapis.com/css2?family=Open+Sans:wght@400;600;700;800&display=swap" rel="stylesheet">
<style>
  :root {
    --backdrop: #d6d2cd;
    --card: #eeeeee;
    --ink: #3a3a3a;
    --ink-soft: #4a4a4a;
    --brand-red: #d7262c;
    --band-dark: #2b2b2d;
    --band-text: #f2f2f2;
  }
  * { margin: 0; padding: 0; box-sizing: border-box; }
  html, body {
    width: 1200px;
    height: 776px;
    overflow: hidden;
    background: var(--backdrop);
    font-family: "Open Sans", Arial, sans-serif;
  }
  .business-card {
    position: absolute;
    left: 100px;
    top: 108px;
    width: 1000px;
    height: 560px;
    background: var(--card);
    border-radius: 26px;
    overflow: hidden;
    box-shadow: 0 10px 30px rgba(0,0,0,0.12);
  }
  .brand {
    position: absolute;
    top: 108px;
    left: 0;
    width: 100%;
    display: flex;
    justify-content: center;
    align-items: center;
    gap: 22px;
  }
  .brand-mark {
    width: 40px;
    height: 40px;
    background: var(--brand-red);
  }
  .brand-name {
    font-weight: 800;
    font-size: 84px;
    line-height: 1;
    letter-spacing: 4px;
    color: var(--ink);
  }
  .holder {
    position: absolute;
    top: 286px;
    right: 520px;
    text-align: right;
    color: var(--ink-soft);
    font-size: 23px;
    line-height: 35px;
  }
  .holder-name {
    font-size: 30px;
    line-height: 40px;
    color: var(--ink);
  }
  .holder-name strong { font-weight: 700; }
  .divider {
    position: absolute;
    left: 500px;
    top: 286px;
    width: 2px;
    height: 156px;
    background: var(--ink);
  }
  .contacts {
    position: absolute;
    left: 528px;
    top: 292px;
    list-style: none;
    color: var(--ink-soft);
    font-size: 21px;
  }
  .contacts li {
    display: flex;
    align-items: center;
    gap: 14px;
    height: 38px;
  }
  .contacts svg { width: 20px; height: 20px; flex: none; }
  .contacts .email { font-size: 20px; }
  .footer-band {
    position: absolute;
    left: 0;
    bottom: 0;
    width: 1000px;
    height: 120px;
  }
  .website {
    position: absolute;
    left: 0;
    bottom: 18px;
    width: 100%;
    text-align: center;
    color: var(--band-text);
    font-size: 24px;
    letter-spacing: 4px;
    font-weight: 600;
  }
</style>
</head>
<body>
  <main class="business-card">
    <div class="brand">
      <span class="brand-mark"></span>
      <span class="brand-name">KORU</span>
    </div>

    <div class="holder">
      <p class="holder-name"><strong>Daniel</strong> Reyes</p>
      <p>Owner / C.E.O.</p>
      <p>Sample Address 4569</p>
      <p>NY Arcvade # 4566</p>
    </div>

    <span class="divider"></span>

    <ul class="contacts">
      <li>
        <svg viewBox="0 0 20 20" aria-hidden="true"><circle cx="10" cy="10" r="10" fill="#3a3a3a"/><path d="M6.5 5.5l2 0 .8 2.3-1.2.9a6 6 0 0 0 2.7 2.7l.9-1.2 2.3.8v2a1 1 0 0 1-1 1A8 8 0 0 1 5.5 6.5a1 1 0 0 1 1-1z" fill="#eee"/></svg>
        <span>123-456-7890</span>
      </li>
      <li>
        <svg viewBox="0 0 20 20" aria-hidden="true"><circle cx="10" cy="10" r="10" fill="#3a3a3a"/><rect x="7" y="4.5" width="6" height="11" rx="1" fill="#eee"/><rect x="8" y="6" width="4" height="6.5" fill="#3a3a3a"/></svg>
        <span>123-456-7890</span>
      </li>
      <li>
        <svg viewBox="0 0 20 20" aria-hidden="true"><circle cx="10" cy="10" r="10" fill="#3a3a3a"/><rect x="5" y="8" width="10" height="6" rx="1" fill="#eee"/><rect x="7" y="5" width="6" height="3" fill="#eee"/></svg>
        <span>123-456-7890</span>
      </li>
      <li>
        <svg viewBox="0 0 20 20" aria-hidden="true"><rect x="2" y="5" width="16" height="10" rx="1" fill="#3a3a3a"/><path d="M2.5 5.5L10 11l7.5-5.5" stroke="#eee" stroke-width="1.4" fill="none"/></svg>
        <span class="email">sample@sample.com</span>
      </li>
    </ul>

    <svg class="footer-band" viewBox="0 0 1000 120" preserveAspectRatio="none" aria-hidden="true">
      <path d="M0 62 Q480 -10 1000 34 L1000 120 L0 120 Z" fill="var(--brand-red)"/>
      <path d="M0 74 Q480 4 1000 48 L1000 120 L0 120 Z" fill="var(--band-dark)"/>
    </svg>
    <p class="website">www.SampleDomain.com</p>
  </main>
</body>
</html>
```